Elegant Business Card for Technology Company

Client is a supplier of innovative industrial communications and automation equipment since 2002. This contest is to gather fresh ideas for a redesign of the existing business card. Client is looking for design that best communicates tagline "Industrial Networking and Computing Specialist".

Design submissions should look modern, clean, elegant and professional. It should not be cluttered. Use white as the primary colour. Orange and black as secondary colour. Refer to jpeg File 1 on the current design.

Fonts used by Client used include Arial Regular, Arial Black, Roboto Regular, Roboto Black and Lato.

The winning design will be sent for offset printing using super white 250gsm artcard paper (open for suggestions).

Target Market(s)

System Engineers, Project Managers, Purchasing Managers from companies providing engineering services for Smart Cities.

Industry/Entity Type

Information Technology

Contact Information for Business Card

Refer to PDF File 3 for Business Card Details. Priority of short contact information would be as follows Name > Job Title > Email > Mobile > Web > Tel > Fax > Business Address >UEN (UEN represents company registration number)

Font styles to use
Sans Serif

Colors
ffffff
f37122
000000
5c5c5c

Requirements
Must have
• Refer to AI File 2 (Company Logo) & PDF File 3 (Information on Namecard)
Should not have
• No QR codes
• No Social Media Icons
• Do not create full Black or Orange colour background

```html
<!DOCTYPE html>
<html lang="en">
<head>
<meta charset="utf-8">
<title>Korvant Asia Pacific – Business Card</title>
<link href="https://fonts.googleapis.com/css2?family=Lato:wght@400;700;900&display=swap" rel="stylesheet">
<style>
  :root {
    --white: #ffffff;
    --orange: #f37122;
    --black: #111111;
    --grey: #5c5c5c;
    --stage: #e9e6e1;
    --card-shadow: 0 10px 26px rgba(0,0,0,.18);
  }
  * { box-sizing: border-box; margin: 0; padding: 0; }
  html, body { width: 1200px; height: 780px; overflow: hidden; }
  body {
    background: var(--stage);
    font-family: "Lato", Arial, sans-serif;
    position: relative;
  }
  .card {
    position: absolute;
    width: 540px;
    height: 310px;
    background: var(--white);
    box-shadow: var(--card-shadow);
    overflow: hidden;
  }
  .card--front { left: 40px; top: 235px; }
  .card--back  { left: 620px; top: 235px; }

  /* Brand mark */
  .brand { display: flex; align-items: center; gap: 12px; }
  .brand__dot { width: 46px; height: 46px; border-radius: 50%; background: var(--orange); }
  .brand__name { font-weight: 900; font-size: 44px; color: var(--black); letter-spacing: 1px; line-height: 1; }

  /* Front */
  .front__top { height: 150px; display: flex; align-items: center; padding-left: 46px; gap: 18px; }
  .front__company { font-size: 19px; color: var(--black); }
  .front__band {
    height: 118px; background: var(--black); color: var(--white);
    display: flex; align-items: center; padding: 0 30px;
  }
  .person { width: 220px; text-align: right; padding-right: 22px; }
  .person__name { font-size: 25px; font-weight: 700; }
  .person__title { font-size: 16px; color: var(--orange); }
  .person__mobile { font-size: 14px; margin-top: 4px; display: flex; justify-content: flex-end; align-items: center; gap: 6px; }
  .divider { width: 1px; height: 70px; background: #777; }
  .contacts { list-style: none; padding-left: 22px; font-size: 13.5px; line-height: 19px; }
  .contacts li { display: flex; align-items: center; gap: 8px; }
  .icon { width: 13px; height: 13px; background: var(--orange); border-radius: 2px; display: inline-flex; align-items: center; justify-content: center; }
  .icon svg { width: 9px; height: 9px; }
  .front__strip {
    height: 42px; background: var(--orange); color: var(--white);
    font-size: 14px; display: flex; align-items: center; justify-content: center;
  }

  /* Back */
  .back__body { height: 262px; padding: 28px 30px 0 34px; position: relative; }
  .back__body .brand__name { font-size: 40px; }
  .back__body .brand__dot { width: 40px; height: 40px; }
  .tagline { margin-top: 14px; font-size: 16px; color: var(--black); padding-bottom: 8px; border-bottom: 2px dotted var(--orange); width: 330px; }
  .services { list-style: none; margin-top: 10px; font-size: 13.5px; line-height: 19px; color: var(--black); }
  .services li { display: flex; align-items: center; gap: 8px; }
  .services li::before { content: ""; width: 7px; height: 7px; border-radius: 50%; background: var(--orange); }
  .back__company { position: absolute; right: 30px; top: 40px; font-size: 16px; color: var(--black); }
  .back__strip {
    height: 48px; background: var(--black); color: var(--white);
    display: flex; align-items: center; padding: 0 26px; font-size: 14px; gap: 24px;
  }
  .back__web { color: var(--orange); }
  .uen__label { color: var(--orange); margin-right: 8px; }
  .badges { margin-left: auto; display: flex; gap: 8px; }
  .badge { width: 18px; height: 18px; border-radius: 3px; background: var(--grey); }
  .badge--orange { background: var(--orange); }
</style>
</head>
<body>

<section class="card card--front" aria-label="Business card front">
  <div class="front__top">
    <div class="brand">
      <span class="brand__dot"></span>
      <span class="brand__name">KVR</span>
    </div>
    <span class="front__company">Korvant Asia Pacific Pte Ltd</span>
  </div>
  <div class="front__band">
    <div class="person">
      <div class="person__name">Daniel Reyes</div>
      <div class="person__title">Sales Manager</div>
      <div class="person__mobile">+65 9123 4567
        <span class="icon"><svg viewBox="0 0 10 10"><rect x="3" y="1" width="4" height="8" rx="1" fill="#fff"/></svg></span>
      </div>
    </div>
    <span class="divider"></span>
    <ul class="contacts">
      <li><span class="icon"><svg viewBox="0 0 10 10"><path d="M2 1h2l1 2-1 1a5 5 0 0 0 2 2l1-1 2 1v2c-4 0-7-3-7-7z" fill="#fff"/></svg></span>+65 6345 2810</li>
      <li><span class="icon"><svg viewBox="0 0 10 10"><rect x="1" y="3" width="8" height="5" fill="#fff"/><rect x="3" y="1" width="4" height="2" fill="#fff"/></svg></span>+65 6345 2811</li>
      <li><span class="icon"><svg viewBox="0 0 10 10"><rect x="1" y="2" width="8" height="6" fill="#fff"/><path d="M1 2l4 3 4-3" stroke="#f37122" fill="none"/></svg></span>sales@korvant.com.sg</li>
      <li><span class="icon"><svg viewBox="0 0 10 10"><circle cx="5" cy="5" r="3.6" stroke="#fff" fill="none"/><path d="M1.4 5h7.2M5 1.4v7.2" stroke="#fff"/></svg></span>www.korvant.com</li>
    </ul>
  </div>
  <div class="front__strip">22 Harlow Link Tech Hub #04-12 (Lobby B), Singapore 417902</div>
</section>

<section class="card card--back" aria-label="Business card back">
  <div class="back__body">
    <div class="brand">
      <span class="brand__dot"></span>
      <span class="brand__name">KVR</span>
    </div>
    <p class="tagline">Industrial Networking and Computing Specialist</p>
    <ul class="services">
      <li>Industrial Ethernet / Wireless / Cellular</li>
      <li>Industrial and Emedded Computing</li>
      <li>Serial / Fieldbus Connectivity</li>
      <li>IP Video Surveillance</li>
      <li>Remote Automation</li>
    </ul>
    <span class="back__company">Korvant Asia Pacific Pte Ltd</span>
  </div>
  <div class="back__strip">
    <span class="back__web">korvant.com</span>
    <span class="uen"><span class="uen__label">UEN No</span>200307415</span>
    <span class="badges">
      <span class="badge"></span>
      <span class="badge"></span>
      <span class="badge badge--orange"></span>
    </span>
  </div>
</section>

</body>
</html>
```